Agriculture Security Company needs a business card design

We need a business card design for a new company based in Seattle calls Ferncrest Guardline LLC. We provide high-end physical security solutions that is geared and focused towards to the marijuana grow operations, wholesalers and distributors. We DO NOT get involved in the retail operations (store fronts). We would like to see designs that incorporate professionalism, reliability, trustworthy and forward thinking as traits of our organization.

Industry/Entity Type

Security

```html
<!DOCTYPE html>
<html lang="en">
<head>
<meta charset="utf-8">
<title>Ferncrest Guardline LLC – Business Card</title>
<link rel="stylesheet" href="https://fonts.googleapis.com/css2?family=Open+Sans:wght@400;600;700&display=swap">
<style>
  :root {
    --bg: #8e8f91;
    --card: #ffffff;
    --green-dark: #176b37;
    --green-light: #76a842;
    --blue: #4a8fcf;
    --ink: #222222;
    --rule: #cfcfcf;
  }
  * { margin: 0; padding: 0; box-sizing: border-box; }
  html, body { width: 1200px; height: 535px; overflow: hidden; }
  body {
    background: var(--bg);
    font-family: "Open Sans", Arial, sans-serif;
    position: relative;
  }
  .card {
    position: absolute;
    width: 508px;
    height: 290px;
    background: var(--card);
    border-radius: 18px;
    overflow: hidden;
  }
  .card--front { left: 86px; top: 133px; }
  .card--back { left: 629px; top: 135px; }
  .card__swoosh { position: absolute; inset: 0; width: 100%; height: 100%; }

  .brand-name {
    position: absolute;
    text-align: center;
    color: var(--green-dark);
    font-weight: 700;
    font-size: 26px;
    line-height: 1.1;
    letter-spacing: 0.5px;
  }
  .card--front .brand-name { left: 40px; width: 230px; top: 118px; }
  .card--back .brand-name { left: 120px; width: 270px; top: 118px; font-size: 30px; }

  .divider {
    position: absolute;
    left: 277px; top: 82px;
    width: 1px; height: 160px;
    background: var(--rule);
  }
  .contact { position: absolute; left: 300px; top: 70px; color: var(--ink); }
  .contact__name { color: var(--green-dark); font-size: 19px; font-weight: 700; line-height: 1.2; }
  .contact__title { color: var(--green-light); font-size: 11.5px; font-weight: 600; margin-bottom: 14px; }
  .contact__company { color: var(--green-dark); font-size: 11.5px; font-weight: 700; line-height: 1.4; }
  .contact__address { font-size: 11.5px; line-height: 1.45; margin-bottom: 12px; }
  .contact__list { list-style: none; font-size: 11.5px; }
  .contact__list li { display: flex; align-items: center; gap: 8px; height: 17px; }
  .contact__list svg { width: 11px; height: 11px; fill: var(--green-dark); flex: none; }

  .web {
    position: absolute;
    left: 0; right: 0; top: 245px;
    text-align: center;
    color: var(--green-dark);
    font-size: 13px;
    font-weight: 600;
    letter-spacing: 2.4px;
  }
</style>
</head>
<body>
  <section class="card card--front">
    <svg class="card__swoosh" viewBox="0 0 508 290" aria-hidden="true">
      <path d="M0 0 H12 Q18 190 66 290 H0 Z" fill="var(--green-dark)"/>
      <path d="M17 0 H22 Q30 190 88 290 H79 Q25 190 17 0 Z" fill="var(--green-light)"/>
    </svg>
    <div class="brand-name">Ferncrest<br>Guardline</div>
    <div class="divider"></div>
    <div class="contact">
      <p class="contact__name">Dana Whitlow</p>
      <p class="contact__title">President</p>
      <p class="contact__company">Ferncrest Guardline LLC</p>
      <p class="contact__address">2150 Harbor Ridge Way<br>Seattle, WA 98121</p>
      <ul class="contact__list">
        <li><svg viewBox="0 0 24 24"><path d="M6.6 10.8c1.4 2.8 3.8 5.1 6.6 6.6l2.2-2.2c.3-.3.7-.4 1-.2 1.1.4 2.3.6 3.6.6.6 0 1 .4 1 1V20c0 .6-.4 1-1 1C10.6 21 3 13.4 3 4c0-.6.4-1 1-1h3.5c.6 0 1 .4 1 1 0 1.3.2 2.5.6 3.6.1.3 0 .7-.2 1l-2.3 2.2z"/></svg>206-555-0147</li>
        <li><svg viewBox="0 0 24 24"><rect x="1" y="4" width="22" height="16" rx="2"/></svg>info@ferncrestguardline.com</li>
        <li><svg viewBox="0 0 24 24"><circle cx="12" cy="12" r="11"/></svg>www.ferncrestguardline.com</li>
      </ul>
    </div>
  </section>

  <section class="card card--back">
    <svg class="card__swoosh" viewBox="0 0 508 290" aria-hidden="true">
      <path d="M410 0 H418 Q468 130 486 290 H478 Q462 130 410 0 Z" fill="var(--blue)"/>
      <path d="M425 0 H508 V290 H492 Q476 130 425 0 Z" fill="var(--green-light)"/>
    </svg>
    <div class="brand-name">Ferncrest<br>Guardline</div>
    <p class="web">www.ferncrestguardline.com</p>
  </section>
</body>
</html>
```